Email design required

We need a design for a paid B2B email campaign and facebook / retargeting banner ads that match the same style.

Website: http://pelmora.staging.hostvantry.com/
Campaign Name: KEX Weariness
Example: http://liftmarrowsites.com/kex-weariness/
- I made this over the weekend. It has the right words, but the style / layout needs to change

Size: 600 pixels wide, no limit on length

Formatting:
Format CSS inline only - This will ensure that size, font family, colour, line height, etc. will all remain the same once it is dropped into our newsletter sending software. See below as an

example,

Here's a mockup of

Target Market(s)

Canadian mortgage brokers

Industry/Entity Type

Campaign

Font styles to use
Sans Serif

Colors
3277b5

Requirements
Must have
• Text from my website example http://liftmarrowsites.com/kex-weariness/
• Otherwise, do whatever you think would look good.

```html
<!DOCTYPE html>
<html lang="en">
<head>
<meta charset="utf-8">
<title>Pelmora – KEX Weariness</title>
<link href="https://fonts.googleapis.com/css2?family=Open+Sans:ital,wght@0,400;0,600;0,700;1,400;1,600&display=swap" rel="stylesheet">
<style>
  :root {
    --page-bg: #2c2c2e;
    --white: #ffffff;
    --brand: #3277b5;
    --brand-text: #2462a8;
    --hero-light: #0a9cf5;
    --hero-dark: #06306d;
    --orange: #f7931e;
    --row-light: #0b84e2;
    --row-dark: #0c3c77;
    --ink: #1d1d1d;
    --grey-text: #6b6b6b;
    --avatar: #555658;
    --footer: #3b3a48;
    --tick: #2bc49b;
  }
  * { box-sizing: border-box; margin: 0; padding: 0; }
  html, body { width: 960px; height: 1200px; overflow: hidden; }
  body { background: var(--page-bg); font-family: "Open Sans", Arial, sans-serif; position: relative; }

  .email {
    position: absolute; left: 240px; top: 94px;
    width: 600px; transform: scale(0.8); transform-origin: top left;
    background: var(--white);
  }

  .masthead { height: 74px; display: flex; align-items: center; justify-content: space-between; padding: 0 36px 0 27px; }
  .brand { display: flex; align-items: center; gap: 6px; color: var(--brand-text); font-weight: 600; font-size: 24px; }
  .brand-mark { width: 16px; height: 16px; background: var(--brand-text); }
  .masthead-link { color: #777; font-size: 14px; text-decoration: none; }

  .hero {
    height: 259px; position: relative; color: var(--white);
    background: radial-gradient(ellipse 60% 70% at 45% 45%, var(--hero-light), #0565c8 55%, var(--hero-dark));
  }
  .hero-title { position: absolute; top: 8px; width: 100%; text-align: center; font-size: 36px; font-weight: 700; }
  .hero-offer { position: absolute; left: 28px; top: 99px; width: 290px; text-align: center; font-size: 14.5px; line-height: 20px; font-weight: 600; }
  .hero-offer .price { color: var(--orange); }
  .hero-button {
    position: absolute; left: 72px; top: 162px; width: 180px; height: 43px; border-radius: 22px;
    background: var(--orange); color: var(--white); font-size: 14px; font-weight: 700;
    display: flex; align-items: center; justify-content: center; text-decoration: none;
  }
  .hero-art { position: absolute; left: 340px; top: 79px; width: 186px; height: 146px; border-radius: 8px; background: linear-gradient(135deg, rgba(255,255,255,.85), rgba(230,238,248,.7)); }

  .band { height: 48px; background: var(--brand); color: var(--white); font-size: 17px; font-weight: 700; display: flex; align-items: center; justify-content: center; }

  .review { height: 169px; position: relative; }
  .review-avatar { position: absolute; left: 60px; top: 17px; width: 124px; height: 124px; border-radius: 50%; background: var(--avatar); }
  .review-quote { position: absolute; left: 247px; top: 28px; width: 320px; font-size: 13px; line-height: 20px; font-style: italic; color: var(--grey-text); }
  .review-name { position: absolute; left: 247px; top: 115px; font-size: 13px; color: var(--grey-text); font-weight: 600; letter-spacing: .2px; }

  .compare { padding: 22px 54px 0 42px; }
  .compare-heads { display: flex; height: 38px; align-items: center; }
  .compare-heads .brand { margin-left: 223px; font-size: 21px; }
  .compare-heads .brand-mark { width: 14px; height: 14px; }
  .other-head { margin-left: auto; margin-right: 4px; font-size: 15px; font-weight: 700; color: var(--ink); }

  .compare-table { width: 504px; border-collapse: collapse; margin-top: 13px; font-size: 13px; }
  .compare-table td { padding: 0 0 0 12px; }
  .compare-table .col-us, .compare-table .col-them { text-align: center; padding: 0; }
  .compare-table .col-label { width: 200px; }
  .compare-table .col-us { width: 154px; }
  .row-light { background: var(--row-light); color: var(--white); height: 37px; }
  .row-dark { background: var(--row-dark); color: var(--white); height: 34px; }
  .row-plain { color: var(--ink); height: 35px; }
  .row-service { background: var(--row-dark); color: var(--white); height: 36px; border-bottom: 1px solid #3f6ea3; font-style: italic; }
  .row-service:last-child { height: 47px; border-bottom: none; }
  .row-service .col-label { padding-left: 44px; line-height: 18px; }
  .row-service .col-them { font-style: normal; }
  .feature { display: flex; align-items: center; gap: 14px; }
  .strong { font-weight: 700; }

  .cta {
    display: flex; flex-direction: column; align-items: center; justify-content: center;
    width: 318px; height: 76px; margin: 23px auto 26px; border-radius: 38px;
    background: var(--orange); color: var(--white); text-decoration: none;
  }
  .cta-main { font-size: 23px; font-weight: 700; letter-spacing: .5px; line-height: 28px; }
  .cta-sub { font-size: 14px; font-weight: 700; }

  .about { padding: 13px 42px 16px; font-size: 13px; line-height: 20px; color: var(--grey-text); }

  .footer { height: 48px; background: var(--footer); color: var(--white); font-size: 13px; display: flex; align-items: center; justify-content: space-between; padding: 0 32px 0 29px; }
  .footer a { color: var(--white); text-decoration: none; }
</style>
</head>
<body>
<main class="email">
  <header class="masthead">
    <div class="brand"><span class="brand-mark"></span>Pelmora</div>
    <a class="masthead-link" href="#">Contact</a>
  </header>

  <section class="hero">
    <h1 class="hero-title">Experiencing KEX Weariness?</h1>
    <p class="hero-offer">Unlimited Notice of Assessment Orders<br>For Just <span class="price">$29 / Month</span></p>
    <a class="hero-button" href="#">Get Started Now</a>
    <div class="hero-art" role="img" aria-label="Illustration of a tired office worker slumped over a desk in a chair"></div>
  </section>

  <h2 class="band">Customer Reviews</h2>
  <section class="review">
    <div class="review-avatar" role="img" aria-label="Customer portrait placeholder"></div>
    <p class="review-quote">I've used a few different services for this and Pelmora is by far the best. Fraction of the cost and I have the required docs within a couple of hours at most. Makes my life so much easier.</p>
    <p class="review-name">Dorian Keswick, Ridgeline Calgary</p>
  </section>

  <h2 class="band">Compare KEX Services</h2>
  <section class="compare">
    <div class="compare-heads">
      <div class="brand"><span class="brand-mark"></span>Pelmora</div>
      <div class="other-head">‘Other Guys’</div>
    </div>
    <table class="compare-table">
      <tr class="row-light">
        <td class="col-label"><span class="feature"><svg width="13" height="13" viewBox="0 0 14 14"><circle cx="7" cy="7" r="5.5" fill="none" stroke="#fff" stroke-width="1.8"/><path d="M4.5 7l2 2 5-5.5" fill="none" stroke="#fff" stroke-width="2"/></svg>Price</span></td>
        <td class="col-us strong">$29 / month</td>
        <td class="col-them">$39 / Order</td>
      </tr>
      <tr class="row-dark">
        <td class="col-label"><span class="feature"><svg width="13" height="13" viewBox="0 0 14 14"><circle cx="7" cy="7" r="5.5" fill="none" stroke="#fff" stroke-width="1.8"/><path d="M4.5 7l2 2 5-5.5" fill="none" stroke="#fff" stroke-width="2"/></svg>Units</span></td>
        <td class="col-us strong">Unlimited</td>
        <td class="col-them">Just One</td>
      </tr>
      <tr class="row-light">
        <td class="col-label"><span class="feature"><svg width="13" height="13" viewBox="0 0 14 14"><circle cx="7" cy="7" r="5.5" fill="none" stroke="#fff" stroke-width="1.8"/><path d="M4.5 7l2 2 5-5.5" fill="none" stroke="#fff" stroke-width="2"/></svg>Turnaround</span></td>
        <td class="col-us strong">4 Hours</td>
        <td class="col-them">1 Day</td>
      </tr>
      <tr class="row-plain">
        <td class="col-label" colspan="3"><span class="feature"><svg width="13" height="13" viewBox="0 0 14 14"><circle cx="7" cy="7" r="5.5" fill="none" stroke="#1d1d1d" stroke-width="1.8"/><path d="M4.5 7l2 2 5-5.5" fill="none" stroke="#1d1d1d" stroke-width="2"/></svg>Other Services</span></td>
      </tr>
      <tr class="row-service">
        <td class="col-label">Document Sorting</td>
        <td class="col-us"><svg width="24" height="20" viewBox="0 0 24 20"><rect x="1" y="4" width="15" height="15" fill="#3a5f86"/><path d="M5 11l4 4 12-13" fill="none" stroke="var(--tick)" stroke-width="3"/></svg></td>
        <td class="col-them">x</td>
      </tr>
      <tr class="row-service">
        <td class="col-label">Lender Fulfillment</td>
        <td class="col-us"><svg width="24" height="20" viewBox="0 0 24 20"><rect x="1" y="4" width="15" height="15" fill="#3a5f86"/><path d="M5 11l4 4 12-13" fill="none" stroke="var(--tick)" stroke-width="3"/></svg></td>
        <td class="col-them">x</td>
      </tr>
      <tr class="row-service">
        <td class="col-label">Closing Package Prepartion<br>And Much More</td>
        <td class="col-us"><svg width="24" height="20" viewBox="0 0 24 20"><rect x="1" y="4" width="15" height="15" fill="#3a5f86"/><path d="M5 11l4 4 12-13" fill="none" stroke="var(--tick)" stroke-width="3"/></svg></td>
        <td class="col-them">x</td>
      </tr>
    </table>
    <a class="cta" href="#"><span class="cta-main">GET STARTED NOW</span><span class="cta-sub">30-Day Money Back Guarantee</span></a>
  </section>

  <h2 class="band">About Us</h2>
  <p class="about">Pelmora provides on-demand administrative support for Mortgage Professionals across Canada. Everything from Notice of Assessment and Title Orders to inbound document sorting and lender fulfilment can be outsouced at a fraction of the cost of a full time administrator.</p>

  <footer class="footer">
    <span>© Pelmora 2016 All rights reserved.</span>
    <a href="#">Unsubscribe here</a>
  </footer>
</main>
</body>
</html>
```